Need website for LED Signs company

Need an web page for a sign company. Basic home page / Tab for photo gallery (projects), tab for other projects could be photo gallery type with the ability for descriptions gallery to be able to have albums (projects) and tab for about us / testimonials Should be easy for me to change with dreamweaver or easy to change add remove content. I will provide pictures and content I would be happy if it could be set up like a template where i can add the content after but i would provide as much content as possible the current page is http://glowcrestsigns.ca examples of my competition:https://metroled.com/led-message-signs/http://www.libertevision.com/https://www.daktronics.com/en-us/products/message-displaysSEO optimized

1 page

• I want to feature LED signs and EMC's the Special projects tab tab will or should be a photo type gallery that is easy to add photos with detailed descriptions
• I do not want to wast peoples time making something similar to what i have now.
• To help me pick a winner Please show links to some of the sites you have created in the past. .

```html
<!DOCTYPE html>
<html lang="en">
<head>
<meta charset="utf-8">
<title>Glowcrest Signs — The Future of L.E.D Technology</title>
<link href="https://fonts.googleapis.com/css2?family=Oswald:wght@400;500;600&family=Poppins:wght@400;500;600&display=swap" rel="stylesheet">
<style>
:root{
  --blue:#0a5bd0;
  --blue-deep:#0b3fa8;
  --blue-band:#0d47b8;
  --navy:#0a1734;
  --ink:#1b1b1b;
  --text:#666;
  --muted:#888;
  --light:#f2f2f2;
  --white:#fff;
  --red:#e52b2b;
  --green:#23b14d;
  --led-blue:#2b7bff;
}
*{margin:0;padding:0;box-sizing:border-box}
html,body{width:1200px;height:3600px;overflow:hidden}
body{position:relative;font-family:'Poppins',sans-serif;color:var(--text);background:var(--white)}
.abs{position:absolute}
h1,h2,h3,.logo{font-family:'Oswald',sans-serif;font-weight:500}
.accent{color:var(--blue)}

/* top bar */
.topbar{left:0;top:0;width:1200px;height:53px;background:var(--blue);color:var(--white);font-size:14px}
.topbar .follow{left:80px;top:16px}
.topbar .social{left:166px;top:13px;width:26px;height:26px;border:2px solid var(--white);border-radius:5px}
.topbar .contact{right:80px;top:15px;display:flex;gap:36px;align-items:center}
.topbar .contact span{display:flex;align-items:center;gap:9px}

/* nav */
.nav{left:0;top:53px;width:1200px;height:110px;background:var(--white)}
.nav .logo{left:78px;top:30px;font-size:38px;color:#333;letter-spacing:.5px;line-height:50px;white-space:nowrap}
.nav ul{left:440px;top:42px;list-style:none;display:flex;gap:34px;font-family:'Oswald',sans-serif;font-size:18px;color:#555}
.nav li.active{color:var(--blue-deep);font-weight:600}
.nav .search{left:1096px;top:42px}

/* hero */
.hero{left:0;top:163px;width:1200px;height:720px;overflow:hidden}
.hero-photo{left:0;top:0;width:1200px;height:720px;background:radial-gradient(ellipse at 50% 35%,#24446f 0%,#0f2546 45%,var(--navy) 100%)}
.hero-curve{left:-300px;top:470px;width:1800px;height:900px;border-radius:50%;background:var(--light)}
.hero h1{left:0;width:1200px;text-align:center;color:var(--white);font-weight:400;font-size:88px;line-height:100px}
.hero .l1{top:162px}
.hero .l2{top:262px}
.led-r{color:var(--red)}.led-g{color:var(--green)}.led-b{color:var(--led-blue)}
.slide-arrow{top:220px;width:52px;height:52px;border-radius:50%;background:rgba(255,255,255,.85)}
.slide-arrow.prev{left:50px}
.slide-arrow.next{left:1096px;background:transparent;border:2px solid rgba(255,255,255,.8)}

.shot{width:192px;height:192px;border-radius:50%;border:7px solid var(--white);box-shadow:0 4px 14px rgba(0,0,0,.25)}
.shot.a{left:132px;top:684px;background:linear-gradient(#6b4a36,#2d2520)}
.shot.b{left:376px;top:684px;background:linear-gradient(#c9c6c0,#5a3c2e)}
.shot.c{left:636px;top:684px;background:linear-gradient(#8fb4d6,#2b2b2b)}
.shot.d{left:880px;top:684px;background:linear-gradient(#c23a2f,#9a8f86)}

/* welcome */
.welcome{left:0;top:883px;width:1200px;height:389px;background:var(--light)}
.welcome h2{left:0;top:66px;width:1200px;text-align:center;font-size:43px;color:var(--ink);font-weight:400}
.welcome p{left:250px;top:146px;width:700px;text-align:center;font-size:13.5px;line-height:23px;color:var(--text)}
.btn{background:var(--blue);color:var(--white);font-size:17px;text-align:center}
.welcome .btn{left:522px;top:274px;width:156px;height:50px;line-height:50px}

/* offers */
.offers{left:0;top:1272px;width:1200px;height:439px;background:var(--white)}
.offers h2{left:0;top:50px;width:1200px;text-align:center;font-size:43px;color:var(--ink);font-weight:400}
.offer{top:144px;width:200px;text-align:center}
.offer .icon{margin:0 auto;width:105px;height:105px;border-radius:50%;border:2px solid #ccc;background:#f4f4f4;display:flex;align-items:center;justify-content:center}
.offer.active .icon{background:var(--blue-deep);border-color:var(--blue-deep)}
.offer h3{margin-top:20px;font-family:'Poppins',sans-serif;font-weight:500;font-size:17px;color:#333;letter-spacing:.5px}
.offer.active h3{color:var(--blue-deep)}
.offer p{margin-top:6px;font-size:12.5px;line-height:20px;color:var(--muted)}
.offer.o1{left:73px}.offer.o2{left:286px}.offer.o3{left:500px}.offer.o4{left:714px}.offer.o5{left:927px}
.car-arrow{top:234px}
.car-arrow.prev{left:56px}.car-arrow.next{left:1118px}

/* services */
.services{left:0;top:1711px;width:1200px;height:696px;background:linear-gradient(180deg,var(--blue-band),#0b3c9e)}
.services h2{left:0;top:58px;width:1200px;text-align:center;font-size:43px;color:var(--white);font-weight:400}
.services .lead{left:290px;top:137px;width:620px;text-align:center;font-size:13.5px;line-height:25px;color:#dfe7ff}
.card{top:228px;width:334px;height:396px;background:var(--white)}
.card .photo{width:334px;height:221px}
.card h3{margin:24px 30px 0;text-align:center;font-family:'Poppins',sans-serif;font-weight:500;font-size:18px;line-height:28px;color:var(--blue-deep)}
.card p{margin:14px 30px 0;text-align:center;font-size:12.5px;line-height:22px;color:var(--muted)}
.card.c1{left:77px}.card.c2{left:434px}.card.c3{left:790px}
.c1 .photo{background:linear-gradient(#0d0d10,#4a1414)}
.c2 .photo{background:linear-gradient(#2c3e64,#b9935c)}
.c3 .photo{background:linear-gradient(#1b4f7a,#3aa0c4)}

/* feedback */
.feedback{left:0;top:2407px;width:1200px;height:725px;background:var(--white)}
.feedback h2{left:0;top:58px;width:1200px;text-align:center;font-size:43px;color:var(--ink);font-weight:400}
.frame{left:77px;top:2556px;width:425px;height:420px}
.frame .portrait{left:0;top:0;width:425px;height:420px;background:linear-gradient(160deg,#d8d3cc,#8f6a52 70%,#f3f1ee)}
.frame .edge-v{left:0;top:120px;width:14px;height:300px;background:var(--blue-deep)}
.frame .edge-h{left:0;top:406px;width:330px;height:14px;background:var(--blue-deep)}
.frame .edge-step{left:316px;top:330px;width:14px;height:90px;background:var(--blue-deep)}
.frame .edge-top{left:316px;top:330px;width:109px;height:14px;background:var(--blue-deep)}
.quote-mark{left:545px;top:2548px;font-family:'Oswald',sans-serif;font-size:76px;color:var(--blue-deep);line-height:76px}
.client-name{left:600px;top:2563px;font-size:23px;font-weight:500;color:var(--blue-deep)}
.client-text{left:600px;top:2628px;width:550px;font-size:13px;line-height:31px;color:var(--muted)}
.client-role{left:600px;top:2864px;font-size:14px;font-weight:600;color:var(--blue-deep)}
.next-btn{left:598px;top:2932px;width:94px;height:40px;border:1px solid var(--blue);background:#dbe6fb;color:var(--blue-deep);font-size:16px;display:flex;align-items:center;justify-content:center;gap:6px}

/* footer */
.footer{left:0;top:3132px;width:1200px;height:408px;background:var(--blue)}
.newsletter{left:77px;top:3048px;width:1046px;height:163px;background:var(--blue-band);border-radius:4px}
.newsletter h2{left:24px;top:24px;font-size:40px;color:var(--white);font-weight:400;letter-spacing:.5px}
.newsletter p{left:24px;top:88px;width:440px;font-size:13px;line-height:23px;color:#dfe7ff}
.subscribe{left:458px;top:40px;width:560px;height:60px;background:var(--white)}
.subscribe .field{left:50px;top:19px;font-size:13px;color:#555}
.subscribe .env{left:14px;top:21px}
.subscribe .btn{left:370px;top:6px;width:182px;height:48px;line-height:48px;font-size:17px;background:var(--blue)}
.foot-col{top:3256px;color:var(--white)}
.foot-col h4{font-family:'Oswald',sans-serif;font-weight:400;font-size:18px;letter-spacing:.5px}
.foot-logo{left:78px;top:3254px;font-family:'Oswald',sans-serif;font-weight:500;font-size:28px;color:var(--white);white-space:nowrap}
.foot-about{left:78px;top:3318px;width:220px;font-size:13px;line-height:24px;color:var(--white)}
.foot-about u{font-weight:600}
.links{left:348px}
.links ul{list-style:none;margin-top:28px;display:grid;grid-template-columns:130px 130px;row-gap:10px;font-size:13px}
.links li::before{content:"- "}
.links li.active{font-weight:600}
.touch{left:617px}
.touch .row{display:flex;gap:16px;align-items:flex-start;font-size:13px;line-height:22px;margin-top:20px}
.touch .row:first-of-type{margin-top:30px}
.sitemap{left:886px}
.map{left:886px;top:3312px;width:245px;height:144px;border-radius:40% 55% 45% 50%;background:radial-gradient(ellipse at 50% 50%,rgba(255,255,255,.28),rgba(255,255,255,.08) 70%,transparent 72%)}
.bottom{left:0;top:3540px;width:1200px;height:60px;background:var(--blue-deep);color:var(--white);font-size:13px}
.bottom .copy{left:78px;top:21px}
.bottom .social{left:1096px;top:17px;width:26px;height:26px;border:2px solid var(--white);border-radius:5px}
</style>
</head>
<body>

<header class="abs topbar">
  <span class="abs follow">Follow On :</span>
  <span class="abs social" aria-label="Social page"></span>
  <div class="abs contact">
    <span><svg width="16" height="16" viewBox="0 0 24 24" fill="none" stroke="#fff" stroke-width="2"><path d="M5 3h4l2 5-3 2a12 12 0 0 0 6 6l2-3 5 2v4a2 2 0 0 1-2 2A18 18 0 0 1 3 5a2 2 0 0 1 2-2z"/></svg>(306) 555-0147</span>
    <span><svg width="18" height="14" viewBox="0 0 24 18" fill="none" stroke="#fff" stroke-width="2"><rect x="1" y="1" width="22" height="16"/><path d="M1 1l11 9 11-9"/></svg>sales@glowcrestsigns.ca</span>
  </div>
</header>

<nav class="abs nav">
  <div class="abs logo">GLOWCREST SIGNS</div>
  <ul class="abs">
    <li class="active">Home</li><li>Services</li><li>About Us</li><li>Gallery</li><li>Downloads</li><li>Technology</li><li>Contact Us</li>
  </ul>
  <svg class="abs search" width="22" height="22" viewBox="0 0 24 24" fill="none" stroke="#0b3fa8" stroke-width="2.4"><circle cx="10" cy="10" r="7"/><path d="M15 15l7 7"/></svg>
</nav>

<section class="abs hero">
  <div class="abs hero-photo" role="img" aria-label="City bridge lit with LED lights at night"></div>
  <div class="abs hero-curve"></div>
  <h1 class="abs l1">The Future of</h1>
  <h1 class="abs l2"><span class="led-r">L</span><span class="led-g">.E.</span><span class="led-b">D</span> technology</h1>
  <svg class="abs slide-arrow prev" viewBox="0 0 52 52"><path d="M29 19l-7 7 7 7" fill="none" stroke="#0b3fa8" stroke-width="3"/></svg>
  <svg class="abs slide-arrow next" viewBox="0 0 52 52"><path d="M23 19l7 7-7 7" fill="none" stroke="#fff" stroke-width="3"/></svg>
</section>

<div class="abs shot a" role="img" aria-label="Storefront with illuminated sign"></div>
<div class="abs shot b" role="img" aria-label="Outdoor LED message board"></div>
<div class="abs shot c" role="img" aria-label="Black Friday billboard display"></div>
<div class="abs shot d" role="img" aria-label="Red storefront LED sign"></div>

<section class="abs welcome">
  <h2 class="abs">WELCOME TO <span class="accent">GLOWCREST SIGNS</span></h2>
  <p class="abs">Glowcrest Signs is not your average L.E.D. Company. Our technology and custom made LED modules have what is takes to make your custom project come to life. Our team will work with you to create your wildest projects. No project is to big or to small. From digital signage, video walls, window signs or custom made DJ booths, Glowcrest Signs will exceed your expectations.</p>
  <div class="abs btn">READ MORE</div>
</section>

<section class="abs offers">
  <h2 class="abs">WHAT WE <span class="accent">OFFERS</span></h2>
  <svg class="abs car-arrow prev" width="20" height="42" viewBox="0 0 20 42"><path d="M16 2L4 21l12 19" fill="none" stroke="#0b3fa8" stroke-width="2"/></svg>
  <svg class="abs car-arrow next" width="20" height="42" viewBox="0 0 20 42"><path d="M4 2l12 19L4 40" fill="none" stroke="#333" stroke-width="2"/></svg>

  <div class="abs offer o1 active">
    <div class="icon"><svg width="48" height="48" viewBox="0 0 48 48" fill="none" stroke="#fff" stroke-width="2.5"><path d="M9 16h30l-3 26H12z"/><path d="M17 20v-6a7 7 0 0 1 14 0v6"/></svg></div>
    <h3>SHOPPING MALLS</h3>
    <p>Shopping Mall, Shopping Plaza, Shopping Centre, Commercial Building...</p>
  </div>
  <div class="abs offer o2">
    <div class="icon"><svg width="50" height="50" viewBox="0 0 50 50" fill="none" stroke="#222" stroke-width="2.5"><path d="M3 19l22-10 22 10-22 10z"/><path d="M13 24v10c6 5 18 5 24 0V24"/><path d="M44 20v12"/></svg></div>
    <h3>SCHOOL</h3>
    <p>Primary School, High School, College, University, Specialized School...</p>
  </div>
  <div class="abs offer o3">
    <div class="icon"><svg width="46" height="46" viewBox="0 0 46 46" fill="none" stroke="#222" stroke-width="2.5"><circle cx="23" cy="23" r="19"/><path d="M4 23h38M23 4v38M10 9c6 7 6 21 0 28M36 9c-6 7-6 21 0 28"/></svg></div>
    <h3>SPORTS</h3>
    <p>Hockey Arena, Aquatic Centre, Velodrome, Baseball Field...</p>
  </div>
  <div class="abs offer o4">
    <div class="icon"><svg width="48" height="48" viewBox="0 0 48 48" fill="none" stroke="#222" stroke-width="2.5"><path d="M4 8h6l5 24h24l4-16H12"/><circle cx="18" cy="39" r="3"/><circle cx="35" cy="39" r="3"/></svg></div>
    <h3>SUPERMARKETS</h3>
    <p>Supermarket, Convenience Store, Food Mart, Food store...</p>
  </div>
  <div class="abs offer o5">
    <div class="icon"><svg width="50" height="50" viewBox="0 0 50 50" fill="none" stroke="#222" stroke-width="2.5"><path d="M7 34a18 18 0 0 1 36 0z"/><path d="M3 38h44"/><circle cx="25" cy="13" r="2.5"/></svg></div>
    <h3>RESTAURANT</h3>
    <p>Restaurant, Bistro, Bar, Coffee Shop, Ice Cream Shop, Buffet...</p>
  </div>
</section>

<section class="abs services">
  <h2 class="abs">OUR SERVICES</h2>
  <p class="abs lead">We are a custom build service. If you can dream it, we can build it. From outdoor displays in your back yard, to massive video walls for indoor and outdoor applications.</p>
  <article class="abs card c1">
    <div class="photo" role="img" aria-label="Outdoor LED ticker display"></div>
    <h3>Outdoor displays in your back yard</h3>
    <p>Lorem ipsum dolor sit amet, consectetur incididunt ut labore et dolore magna aliqua...</p>
  </article>
  <article class="abs card c2">
    <div class="photo" role="img" aria-label="Villa courtyard with pool at dusk"></div>
    <h3>Massive video walls for indoor</h3>
    <p>Lorem ipsum dolor sit amet, consectetur incididunt ut labore et dolore magna aliqua...</p>
  </article>
  <article class="abs card c3">
    <div class="photo" role="img" aria-label="Cylindrical aquarium installation in a lobby"></div>
    <h3>outdoor applications</h3>
    <p>Lorem ipsum dolor sit amet, consectetur adipiscing elit, sed do eiusmod tempor incididunt ut labore et dolore magna aliqua.</p>
  </article>
</section>

<section class="abs feedback">
  <h2 class="abs">CLIENTS <span class="accent">FEEDBACK</span></h2>
</section>
<div class="abs frame">
  <div class="abs portrait" role="img" aria-label="Portrait of the client giving feedback"></div>
  <div class="abs edge-v"></div>
  <div class="abs edge-h"></div>
  <div class="abs edge-step"></div>
  <div class="abs edge-top"></div>
</div>
<div class="abs quote-mark">&ldquo;</div>
<div class="abs client-name">Marla Penrose</div>
<p class="abs client-text">Lorem ipsum dolor sit amet, consectetur adipiscing elit, sed do eiusmod tempor incididunt ut labore et dolore magna aliqua. Ut enim ad minim veniam, quis nostrud exercitation ullamco laboris nisi ut aliquip ex ea commodo consequat. Duis aute irure dolor in reprehenderit in voluptate velit esse cillum dolore eu fugiat nulla pariatur. Excepteur sint occaecat cupidatat non proident, sunt in culpa qui officia deserunt mollit anim id est laborum.Sed ut perspiciatis unde omnis iste natus error sit voluptatem accusantium doloremque laudantium.</p>
<div class="abs client-role">Founder of brightlane.com</div>
<div class="abs next-btn">NEXT <svg width="8" height="12" viewBox="0 0 8 12"><path d="M1 1l5 5-5 5" fill="none" stroke="#0b3fa8" stroke-width="2"/></svg></div>

<footer class="abs footer"></footer>

<section class="abs newsletter">
  <h2 class="abs">SUBCRIBE NEWSLETTER</h2>
  <p class="abs">Lorem ipsum dolor sit amet, consectetur adipiscing elit, sed do eiusmod tempor incididunt ut labore et dolore magna aliqua.</p>
  <div class="abs subscribe">
    <svg class="abs env" width="22" height="16" viewBox="0 0 24 18"><rect x="0" y="0" width="24" height="18" fill="#0b3fa8"/><path d="M1 1l11 9 11-9" fill="none" stroke="#fff" stroke-width="2"/></svg>
    <span class="abs field">Enter Email :</span>
    <div class="abs btn">SUBSCRIBE</div>
  </div>
</section>

<div class="abs foot-logo">GLOWCREST SIGNS</div>
<p class="abs foot-about">Lorem ipsum dolor sit amet, consectetur adipiscing elit, sed do eiusmod tempor incididunt ut labore et dolor... <u>VIEW GALLERY</u></p>

<div class="abs foot-col links">
  <h4>QUICK LINKS</h4>
  <ul>
    <li class="active">Home</li><li>Download</li>
    <li>About</li><li>Technology</li>
    <li>Services</li><li>Contact us</li>
    <li>Gallery</li>
  </ul>
</div>

<div class="abs foot-col touch">
  <h4>GET IN TOUCH</h4>
  <div class="row"><svg width="18" height="22" viewBox="0 0 18 22"><path d="M9 1a7 7 0 0 1 7 7c0 5-7 13-7 13S2 13 2 8a7 7 0 0 1 7-7z" fill="#fff"/><circle cx="9" cy="8" r="2.5" fill="#0a5bd0"/></svg><span>Riverton,<br>Saskatchewan S7X 0A1</span></div>
  <div class="row"><svg width="18" height="18" viewBox="0 0 24 24"><path d="M5 3h4l2 5-3 2a12 12 0 0 0 6 6l2-3 5 2v4a2 2 0 0 1-2 2A18 18 0 0 1 3 5a2 2 0 0 1 2-2z" fill="#fff"/></svg><span>(306) 555-0147</span></div>
  <div class="row"><svg width="18" height="14" viewBox="0 0 24 18" fill="none" stroke="#fff" stroke-width="2"><rect x="1" y="1" width="22" height="16"/><path d="M1 1l11 9 11-9"/></svg><span>sales@glowcrestsigns.ca</span></div>
</div>

<div class="abs foot-col sitemap"><h4>SITE MAP</h4></div>
<div class="abs map" role="img" aria-label="World map showing service locations"></div>

<div class="abs bottom">
  <span class="abs copy">© 2019 &nbsp;<b>GLOWCREST SIGNS.</b> All rights reserved.</span>
  <span class="abs social" aria-label="Social page"></span>
</div>

</body>
</html>
```